Business Card Design & Gift cards, Gift Cert, Donation Card

Retail Gift Store-in addition to Business Cards we'd like sequenced 2 sided Gift cards, Gift Certificate Cards, and Donation Cards.please see examples and email for clarificationlogos attached with examples-
Gift Card, Gift Certificate and Donation Card will all be same style just differant upper right title, with back side info as example.
business card, as example is single sided.
looking for additional ideas for layout

Industry/Entity Type

Business

Contact Information for Business Card

211 Newman St.East Tawas, MI 48730989.362.8730Office@BrewKrew.com

Requirements
Must have
• Blue as per example
• Logos provided
• like gradiant background

```html
<!DOCTYPE html>
<html lang="en">
<head>
<meta charset="utf-8">
<title>Tillow Marsh – Business Card &amp; Gift Card</title>
<link rel="stylesheet" href="https://fonts.googleapis.com/css2?family=Comic+Neue:wght@400;700&family=PT+Sans&display=swap">
<style>
  :root {
    --stage: #3a3a3a;
    --card: #ffffff;
    --ink: #1a1a1a;
    --ink-soft: #555555;
    --rule: #6a6a6a;
    --brand-blue: #1f2fc4;
    --brand-faint: #e6eaf8;
  }
  * { margin: 0; padding: 0; box-sizing: border-box; }
  html, body { width: 1105px; height: 1200px; overflow: hidden; }
  body { background: var(--stage); position: relative; }

  .card {
    position: absolute;
    left: 196px;
    width: 718px;
    height: 410px;
    background: var(--card);
    border-radius: 22px;
    overflow: hidden;
  }
  .card--front { top: 146px; }
  .card--back { top: 602px; }
  .card * { position: absolute; }

  /* Front */
  .brand-name {
    left: 36px; top: 168px;
    font-family: "Comic Neue", cursive;
    font-weight: 400;
    font-size: 52px;
    line-height: 1;
    color: var(--ink);
    letter-spacing: 1px;
  }
  .brand-dot { left: 556px; top: 36px; }
  .divider { left: 36px; top: 256px; width: 644px; height: 2px; background: var(--rule); }
  .contact {
    left: 36px; top: 274px;
    font-family: "PT Sans", sans-serif;
    font-size: 21px;
    line-height: 26.5px;
    color: var(--ink-soft);
    list-style: none;
  }
  .contact li { position: relative; display: flex; align-items: center; gap: 8px; }
  .contact svg { position: static; }
  .offerings {
    right: 38px; top: 274px;
    font-family: "Comic Neue", cursive;
    font-size: 22px;
    line-height: 26.5px;
    color: var(--ink-soft);
    text-align: right;
    list-style: none;
  }
  .offerings li { position: relative; }

  /* Back */
  .brand-faint { left: 274px; top: 116px; }
  .card-number {
    right: 38px; top: 38px;
    font-family: "Comic Neue", cursive;
    font-size: 18px;
    color: var(--ink);
  }
  .field-label {
    font-family: "Comic Neue", cursive;
    color: var(--ink);
    white-space: pre;
  }
  .field-label--large { font-size: 27px; }
  .field-label--small { font-size: 21px; }
  .field-line { height: 1.5px; background: var(--ink-soft); }
</style>
</head>
<body>

<section class="card card--front" aria-label="Business card">
  <div class="brand-name">Tillow Marsh</div>
  <svg class="brand-dot" width="110" height="110" viewBox="0 0 110 110" aria-hidden="true">
    <circle cx="55" cy="55" r="50" fill="var(--brand-blue)"/>
  </svg>
  <div class="divider"></div>
  <ul class="contact">
    <li>482 Larkfield Ave.</li>
    <li>Cedar Hollow, MI 48762</li>
    <li>
      <svg width="17" height="17" viewBox="0 0 24 24" aria-hidden="true"><path fill="#222" d="M6.6 10.8a15.2 15.2 0 0 0 6.6 6.6l2.2-2.2c.3-.3.7-.4 1-.2 1.1.4 2.3.6 3.6.6.6 0 1 .4 1 1V20c0 .6-.4 1-1 1C10.6 21 3 13.4 3 4c0-.6.4-1 1-1h3.5c.6 0 1 .4 1 1 0 1.3.2 2.5.6 3.6.1.3 0 .7-.2 1z"/></svg>
      989.517.4296
    </li>
    <li>
      <svg width="17" height="13" viewBox="0 0 24 18" aria-hidden="true"><path fill="#222" d="M0 0h24v18H0z"/><path fill="none" stroke="#fff" stroke-width="2" d="M1 1l11 9 11-9"/></svg>
      Office@TillowMarsh.com
    </li>
  </ul>
  <ul class="offerings">
    <li>Gourmet Food</li>
    <li>Fine Wines | Gift Baskets</li>
    <li>Kitchen &amp; Bath Accessories</li>
    <li>Candles | Cards | Soaps</li>
  </ul>
</section>

<section class="card card--back" aria-label="Gift card back">
  <svg class="brand-faint" width="220" height="220" viewBox="0 0 220 220" aria-hidden="true">
    <circle cx="110" cy="110" r="108" fill="var(--brand-faint)"/>
  </svg>
  <div class="card-number">Card Number : 58724</div>

  <div class="field-label field-label--large" style="left:58px; top:80px;">To :</div>
  <div class="field-line" style="left:124px; top:105px; width:543px;"></div>

  <div class="field-label field-label--large" style="left:58px; top:138px;">Form :</div>
  <div class="field-line" style="left:153px; top:163px; width:514px;"></div>

  <div class="field-label field-label--small" style="left:56px; top:225px;">Date  Issued :</div>
  <div class="field-line" style="left:204px; top:246px; width:473px;"></div>

  <div class="field-label field-label--small" style="left:56px; top:273px;">Expiration Date :</div>
  <div class="field-line" style="left:235px; top:294px; width:442px;"></div>

  <div class="field-label field-label--small" style="left:56px; top:321px;">Employee :</div>
  <div class="field-line" style="left:186px; top:342px; width:491px;"></div>
</section>

</body>
</html>
```